Velundra Jobs portal

Velundra Jobs is a job portal connecting job seekers and companies offering part time jobs in the Mena region, starting in the UAE. We would like to see designs that use the color blue. We have attached images to give an idea what the website should look like. When a company posts a job the job seekers are not allowed to see which company has posted a job. There should also be a coinvex gateway. On the landing page we want a catching picture that we will send.

Target Market(s)

Students and promotional workers

Logo Text

Velundra Jobs

Coding

Coded - Design and coding required

Number of Pages Required

4 page

Font styles to use
Sans Serif

Colors
33a6d7
0692cd
85cae6

```html
<!DOCTYPE html>
<html lang="en">
<head>
<meta charset="utf-8">
<title>Velundra Jobs</title>
<link href="https://fonts.googleapis.com/css2?family=Open+Sans:wght@400;600;700&display=swap" rel="stylesheet">
<style>
:root{
  --teal:#4ec9c5;
  --navy:#2a4a9e;
  --footer:#3461b0;
  --pink:#e2417f;
  --panel:#e9e9e9;
  --row-alt:#e9e9e9;
  --line:#d8d8d8;
  --text:#555;
  --white:#fff;
}
*{box-sizing:border-box;margin:0;padding:0}
html,body{width:1097px;height:1200px;overflow:hidden;background:var(--white);font-family:"Open Sans",Arial,sans-serif;color:var(--text)}
.page{position:relative;width:1097px;height:1200px}
.hero{position:absolute;left:0;top:0;width:1097px;height:184px;background:linear-gradient(100deg,#8b8f9c 0%,#c8b3b0 30%,#b9c4d2 55%,#8093b0 80%,#6c7f9f 100%)}
.topbar{position:absolute;left:48px;top:34px;width:1000px;height:108px;border-radius:54px;background:rgba(255,255,255,.28);border:1px solid rgba(255,255,255,.45)}
.brand{position:absolute;left:136px;top:35px;width:104px;height:107px;background:var(--white);display:flex;align-items:flex-end;justify-content:center;padding-bottom:14px;font-size:18px;font-weight:400;color:#2fa7c9}
.nav{position:absolute;top:81px;font-size:12px;font-weight:600;color:var(--white);letter-spacing:.2px}
.search{position:absolute;left:579px;top:73px;width:142px;height:30px;border:1px solid rgba(255,255,255,.9)}
.search svg{position:absolute;right:10px;top:7px}
.bell{position:absolute;left:752px;top:72px}
.badge{position:absolute;left:771px;top:63px;width:24px;height:24px;border-radius:50%;background:var(--navy);border:1px solid #fff;color:#fff;font-size:10px;text-align:center;line-height:22px}
.avatar{position:absolute;left:818px;top:54px;width:70px;height:70px;border-radius:50%;border:3px solid #fff;background:linear-gradient(160deg,#8a5a3a,#c98b5e)}
.logout{position:absolute;left:921px;top:70px;width:85px;height:33px;background:var(--pink);border:2px solid #fff;color:#fff;font-size:12px;font-weight:600;text-align:center;line-height:29px}

.sidebar{position:absolute;left:47px;top:209px;width:269px;height:876px;background:var(--panel)}
.sidebar h2{height:45px;background:var(--teal);color:#fff;font-size:16px;font-weight:600;padding-left:35px;line-height:45px}
.cat{height:42.2px;border-bottom:1px solid var(--line);font-size:12px;padding-left:37px;line-height:42px}

.filter{position:absolute;left:343px;top:210px;width:705px;height:95px;background:var(--panel)}
.field{position:absolute;top:30px;width:194px;height:36px;background:#fff;font-size:12px;color:#999;padding-left:16px;line-height:36px}
.field svg{position:absolute;right:16px;top:15px}
.filter-btn{position:absolute;left:527px;top:25px;width:147px;height:45px;background:var(--navy);border:2px solid #fff;color:#fff;font-size:15px;font-weight:600;display:flex;align-items:center;justify-content:center;gap:10px;box-shadow:0 1px 3px rgba(0,0,0,.15)}

.jobs{position:absolute;left:343px;top:333px;width:705px}
.row{display:grid;grid-template-columns:245px 173px 160px 127px;height:42.4px;align-items:center;font-size:12px}
.row>span{height:100%;display:flex;align-items:center;border-right:1px solid var(--line)}
.row>span:last-child{border-right:0;justify-content:center}
.row .c1{padding-left:23px}.row .c2{padding-left:17px}.row .c3{padding-left:13px}
.row:nth-child(even){background:var(--row-alt)}
.row:nth-child(odd){background:#fff}
.head{height:43px;background:var(--teal)!important;color:#fff;font-size:15px;font-weight:600}
.head>span{border-right:1px solid rgba(255,255,255,.4)}
.apply{width:92px;height:26px;background:var(--navy);color:#fff;font-size:12.5px;font-weight:400;text-align:center;line-height:26px}

.featured{position:absolute;left:343px;top:789px;width:705px;height:296px;background:var(--panel)}
.featured h2{height:40px;background:var(--teal);color:#fff;font-size:15px;font-weight:600;padding-left:26px;line-height:40px}
.arrows{position:absolute;right:12px;top:12px}
.card{position:absolute;top:67px;width:202px;height:210px;background:#efefef;border:1px solid #e2e2e2}
.card .photo{position:absolute;left:5px;top:4px;width:192px;height:164px}
.card p{position:absolute;left:0;right:0;bottom:11px;text-align:center;font-size:13px;font-weight:600;color:#555}

.footer{position:absolute;left:0;top:1112px;width:1097px;height:88px;background:var(--footer);color:#fff}
.copy{position:absolute;left:91px;top:32px;font-size:12px}
.social{position:absolute;left:906px;top:19px;display:flex;gap:10px}
.social i{width:16px;height:16px;border-radius:50%;background:#fff}
.links{position:absolute;right:91px;top:48px;font-size:12px}
.links .sep{font-size:9px;margin:0 4px}
</style>
</head>
<body>
<div class="page">
  <header class="hero" role="img" aria-label="Photo of a hand typing on a keyboard"></header>
  <div class="topbar"></div>
  <div class="brand">Velundra</div>
  <span class="nav" style="left:386px">ABOUT US</span>
  <span class="nav" style="left:470px">CONTACT US</span>
  <div class="search"><svg width="14" height="14" viewBox="0 0 14 14"><circle cx="6" cy="6" r="4.5" fill="none" stroke="#2a4a9e" stroke-width="2"/><line x1="9.3" y1="9.3" x2="13" y2="13" stroke="#2a4a9e" stroke-width="2.4"/></svg></div>
  <svg class="bell" width="34" height="36" viewBox="0 0 34 36"><path d="M8 26V16a9 9 0 0 1 18 0v10l4 4H4z" fill="none" stroke="#fff" stroke-width="2"/><path d="M13 32a4 4 0 0 0 8 0" fill="none" stroke="#fff" stroke-width="2"/></svg>
  <div class="badge">23</div>
  <div class="avatar" role="img" aria-label="User profile photo"></div>
  <div class="logout">LOG OUT</div>

  <aside class="sidebar">
    <h2>CATEGORIES</h2>
    <div style="height:15px"></div>
    <div class="cat">Banking Jobs</div>
    <div class="cat">Government Jobs</div>
    <div class="cat">IT Jobs</div>
    <div class="cat">Core Jobs</div>
    <div class="cat">Web Designing</div>
    <div class="cat">Hardware</div>
    <div class="cat">Software</div>
    <div class="cat">Core Jobs</div>
    <div class="cat">Web Designing</div>
    <div class="cat">Hardware</div>
  </aside>

  <section class="filter">
    <div class="field" style="left:35px">WORK OFFERED</div>
    <div class="field" style="left:269px">LOCATION<svg width="10" height="6" viewBox="0 0 10 6"><path d="M0 0h10L5 6z" fill="#aaa"/></svg></div>
    <div class="filter-btn">FILTER JOBS <svg width="14" height="14" viewBox="0 0 14 14"><path d="M0 0h14L8.5 6.5V14L5.5 12V6.5z" fill="#fff"/></svg></div>
  </section>

  <section class="jobs">
    <div class="row head"><span class="c1">JOB TITLE</span><span class="c2">DUE DATE</span><span class="c3">LOCATION</span><span></span></div>
    <div class="row"><span class="c1">Job Title Number 1</span><span class="c2">23 Jan 2015</span><span class="c3">Dubai</span><span><span class="apply">Apply Now</span></span></div>
    <div class="row"><span class="c1">Job Title Number 1</span><span class="c2">23 Jan 2015</span><span class="c3">Dubai</span><span><span class="apply">Apply Now</span></span></div>
    <div class="row"><span class="c1">Job Title Number 1</span><span class="c2">23 Jan 2015</span><span class="c3">Dubai</span><span><span class="apply">Apply Now</span></span></div>
    <div class="row"><span class="c1">Job Title Number 1</span><span class="c2">23 Jan 2015</span><span class="c3">Dubai</span><span><span class="apply">Apply Now</span></span></div>
    <div class="row"><span class="c1">Job Title Number 1</span><span class="c2">23 Jan 2015</span><span class="c3">Dubai</span><span><span class="apply">Apply Now</span></span></div>
    <div class="row"><span class="c1">Job Title Number 1</span><span class="c2">23 Jan 2015</span><span class="c3">Dubai</span><span><span class="apply">Apply Now</span></span></div>
    <div class="row"><span class="c1">Job Title Number 1</span><span class="c2">23 Jan 2015</span><span class="c3">Dubai</span><span><span class="apply">Apply Now</span></span></div>
    <div class="row"><span class="c1">Job Title Number 1</span><span class="c2">23 Jan 2015</span><span class="c3">Dubai</span><span><span class="apply">Apply Now</span></span></div>
    <div class="row"><span class="c1">Job Title Number 1</span><span class="c2">23 Jan 2015</span><span class="c3">Dubai</span><span><span class="apply">Apply Now</span></span></div>
  </section>

  <section class="featured">
    <h2>FEATURED JOB PROVIDERS</h2>
    <svg class="arrows" width="36" height="16" viewBox="0 0 36 16"><path d="M7 2L2 8l5 6M29 2l5 6-5 6" fill="none" stroke="#fff" stroke-width="2"/></svg>
    <div class="card" style="left:22px"><div class="photo" role="img" aria-label="Business people meeting at an office desk" style="background:linear-gradient(135deg,#dfe3e6,#3a3f4d 60%,#c9ccd2)"></div><p>FINIBUS BONORUM</p></div>
    <div class="card" style="left:252px"><div class="photo" role="img" aria-label="Team reviewing documents at a table" style="background:linear-gradient(135deg,#2e2f36,#a9b4c6 50%,#4a4b52)"></div><p>FINIBUS BONORUM</p></div>
    <div class="card" style="left:482px"><div class="photo" role="img" aria-label="Business partners shaking hands" style="background:linear-gradient(135deg,#c6d2de,#2d3342 55%,#a8b6c4)"></div><p>FINIBUS BONORUM</p></div>
  </section>

  <footer class="footer">
    <div class="copy">© Velundra 2015 ,All rights reserved.</div>
    <div class="social"><i></i><i></i><i></i><i></i></div>
    <div class="links">About Us<span class="sep">|</span>Terms and Conditions<span class="sep">|</span>Sitemap</div>
  </footer>
</div>
</body>
</html>
```